Marta's Dwellings website

We need a simple website for our property investment business in the UK. We basically need our contact details and brief description.We have the company logo already done (via ArtFlockly) so please use these:https://drive.google.com/drive/folders/1szJ3iRhelElZ40NIFT7w-c14MaY3Y_oV?usp=sharingYou could use some stock photos of UK houses for now.Let me know when to provide more detailed descriptions, etc

Coding

Coded - Design and coding required

Number of Pages Required

1 page

Colors

Designer to choose colors to be used in the design.

```html
<!DOCTYPE html>
<html lang="en">
<head>
<meta charset="utf-8">
<title>Marta's Dwellings</title>
<link rel="stylesheet" href="https://fonts.googleapis.com/css2?family=Poppins:wght@400;500;600;700&family=Lato:wght@400;700&family=Montserrat:wght@400;500;600;700&display=swap">
<style>
:root{
  --black:#000;
  --ink:#111;
  --dark:#1b1b1b;
  --text:#555;
  --muted:#777;
  --white:#fff;
  --accent:#1f5fd0;
  --sky:#7fa9d6;
  --brick:#8a4a34;
  --grass:#4f7a32;
  --pool:#2f7fc4;
}
*{box-sizing:border-box;margin:0;padding:0}
html,body{width:1200px;height:3932px;overflow:hidden;background:var(--white)}
body{position:relative;font-family:'Poppins',sans-serif;color:var(--ink)}
.abs{position:absolute}

/* header */
.site-header{left:0;top:0;width:1200px;height:165px;background:var(--ink)}
.brand{left:90px;top:40px;display:flex;align-items:center;gap:12px;color:var(--white);font-family:'Montserrat',sans-serif;font-weight:500;font-size:17px;letter-spacing:6px}
.brand .mark{width:44px;height:44px;background:var(--white)}
.contact-bar{right:90px;top:43px;display:flex;gap:22px;color:var(--white);font-family:'Montserrat',sans-serif;font-weight:600;font-size:15px;align-items:center}
.contact-bar span{display:flex;align-items:center;gap:10px}
.main-nav{right:90px;top:104px;display:flex;gap:40px;color:var(--white);font-family:'Montserrat',sans-serif;font-weight:600;font-size:15px}

/* hero */
.hero{left:0;top:165px;width:1200px;height:745px;background:linear-gradient(180deg,#3a3532 0%,#4d3b30 40%,#3e4a2e 75%,#2c3622 100%)}
.hero-divider{left:0;top:735px;width:1200px;height:180px}
.hero-kicker{left:0;top:366px;width:1200px;text-align:center;color:var(--white);font-family:'Montserrat',sans-serif;font-weight:600;font-size:31px;letter-spacing:2px}
.hero-title{left:0;top:415px;width:1200px;text-align:center;color:var(--white);font-family:'Montserrat',sans-serif;font-weight:700;font-size:84px;letter-spacing:5px}

/* about */
.section-title{left:0;width:1200px;text-align:center;font-weight:600}
.about-title{top:983px;font-size:43px;font-family:'Montserrat',sans-serif;font-weight:700}
.about-text{left:185px;top:1053px;width:830px;text-align:center;font-family:'Lato',sans-serif;font-size:16px;line-height:30.5px;color:var(--text)}
.about-photo{left:89px;top:1183px;width:720px;height:475px;background:linear-gradient(180deg,#9fc3e0 0%,#5f8a4a 35%,#a06a48 55%,var(--pool) 80%,#c9b79c 100%)}
.about-card{left:669px;top:1225px;width:531px;height:391px;background:var(--white);box-shadow:0 4px 18px rgba(0,0,0,.12)}
.about-card h2{position:absolute;left:54px;top:48px;font-family:'Josefin Sans','Poppins',sans-serif;font-weight:600;font-size:44px}
.about-card p{position:absolute;left:59px;top:117px;width:365px;font-family:'Lato',sans-serif;font-size:15px;line-height:28.5px;color:var(--text)}
.btn{display:flex;align-items:center;justify-content:center;background:var(--ink);color:var(--white);border-radius:30px;font-weight:600}
.about-card .btn{position:absolute;left:55px;top:279px;width:171px;height:57px;font-size:16px}

/* properties */
.properties-bg{left:0;top:1745px;width:1200px;height:935px}
.properties-title{top:1856px;font-size:45px;color:var(--white);font-weight:500}
.property{width:328px;height:264px}
.property.sky{background:linear-gradient(180deg,var(--sky) 0%,#c8d9e6 30%,var(--brick) 55%,var(--grass) 100%)}
.property.dark{background:linear-gradient(180deg,#2a2a28,#222 60%,#1f2418)}
.property.street{background:linear-gradient(180deg,#b7c4d2 0%,#d5d0c6 35%,#7c6050 70%,#3d3a36 100%)}
.property.brick{background:linear-gradient(180deg,#7b93a8 0%,#8a4a34 35%,#7a3e2c 75%,#4e5a36 100%)}
.listing{color:var(--white);text-align:center;padding-top:70px}
.listing h3{font-weight:600;font-size:17px}
.listing .addr{font-size:10px;margin-top:4px;font-family:'Montserrat',sans-serif}
.listing .meta{font-size:9px;margin-top:8px;font-family:'Montserrat',sans-serif}
.listing .price{font-size:18px;font-weight:600;margin-top:10px}
.listing .actions{display:flex;justify-content:center;gap:20px;margin-top:10px}
.listing .actions i{width:26px;height:26px;border-radius:50%;background:var(--white);display:block}
.dots{left:553px;top:2551px;display:flex;gap:12px}
.dots i{width:22px;height:3px;background:var(--white);display:block}
.dots i.on{background:var(--accent)}

/* blog */
.blog-title{top:2752px;font-size:44px;font-weight:500}
.blog-card{background:var(--white);box-shadow:0 2px 12px rgba(0,0,0,.15);padding:10px}
.blog-card div{width:100%;height:100%}
.blog-main div{background:linear-gradient(180deg,#5f7fae 0%,#3f5f8f 30%,#7a5a3a 55%,#f2b25c 65%,#4d7a2a 85%,#3c6420 100%)}
.blog-side div{background:linear-gradient(180deg,#d8c6a8,#b9814e 60%,#efe2cc)}
.blog-side.r div{background:linear-gradient(180deg,#6a2e22,#b23a2a 50%,#e9e1d6)}
.blog-text{left:699px;top:2870px;width:330px}
.blog-text h3{font-weight:500;font-size:26px}
.blog-text .lead{font-family:'Montserrat',sans-serif;font-weight:600;font-size:13px;line-height:22px;color:#444;margin-top:16px}
.blog-text .body{font-family:'Montserrat',sans-serif;font-size:13px;line-height:22px;color:var(--muted);margin-top:16px}
.blog-text .btn{width:164px;height:43px;font-size:17px;margin-top:25px}
.arrow{width:24px;height:24px}

/* footer */
.footer-bg{left:0;top:3270px;width:1200px;height:662px}
.footer{color:var(--white);font-family:'Montserrat',sans-serif}
.footer-brand{left:110px;top:3480px;display:flex;align-items:center;gap:12px;font-weight:500;font-size:17px;letter-spacing:6px}
.footer-brand .mark{width:40px;height:40px;background:var(--white)}
.contact-list{left:104px;top:3580px;width:380px;font-size:17px;line-height:26px}
.contact-list li{list-style:none;display:flex;gap:18px;margin-bottom:10px}
.contact-list svg{flex:none;margin-top:4px}
.footer h4{font-size:21px;font-weight:600}
.signup{left:544px;top:3492px;width:330px}
.signup p{font-size:14px;line-height:24px;margin-top:32px}
.signup .field{width:307px;height:37px;border-radius:20px;background:var(--white);color:#888;font-size:10px;padding:12px 18px;margin-top:18px}
.signup .sub{width:113px;height:37px;border-radius:20px;background:#1a1a1a;display:flex;align-items:center;justify-content:center;font-weight:700;font-size:13px;margin-top:18px}
.quick-links{left:960px;top:3492px}
.quick-links ul{list-style:none;margin-top:22px;font-size:15px;line-height:31.5px}
.footer-rule{left:0;top:3793px;width:1200px;height:1px;background:#333}
.copyright{left:0;top:3817px;width:1200px;text-align:center;font-size:16px;color:var(--white);font-family:'Montserrat',sans-serif}
.social{left:525px;top:3861px;display:flex;gap:4px}
.social i{width:34px;height:34px;border-radius:50%;border:1.5px solid var(--white);display:block}
</style>
</head>
<body>

<header class="site-header abs">
  <div class="brand abs"><span class="mark"></span>MARTA'S DWELLINGS</div>
  <div class="contact-bar abs">
    <span><svg width="20" height="20" viewBox="0 0 24 24" fill="none" stroke="#fff" stroke-width="1.5"><path d="M5 3h4l2 5-3 2a12 12 0 0 0 6 6l2-3 5 2v4a2 2 0 0 1-2 2A18 18 0 0 1 3 5a2 2 0 0 1 2-2z"/></svg>555 010 2040</span>
    <span><svg width="24" height="18" viewBox="0 0 24 18" fill="none" stroke="#fff" stroke-width="1.5"><rect x="1" y="1" width="22" height="16"/><path d="M1 1l11 9 11-9"/></svg>info@martasdwellings-mail.net</span>
  </div>
  <nav class="main-nav abs"><span>Home</span><span>About Us</span><span>Our Properties</span><span>Blog</span><span>Contact Us</span></nav>
</header>

<section class="hero abs" role="img" aria-label="Photo of a red-brick English house with a white picket gate, darkened"></section>
<svg class="hero-divider abs" viewBox="0 0 1200 180" aria-hidden="true">
  <polygon points="0,10 600,148 1200,10 1200,180 0,180" fill="#fff"/>
  <polygon points="0,14 600,160 1200,10 1200,22 610,172 600,178 0,26" fill="#000"/>
</svg>
<div class="hero-kicker abs">WELCOME TO</div>
<h1 class="hero-title abs">Marta's Dwellings</h1>

<h2 class="section-title about-title abs">ABOUT US</h2>
<p class="about-text abs">Lorem Ipsum is simply dummy text of the printing and typesetting industry. Lorem Ipsum has been the industry's standard dummy text ever since the 1500s, when an unknown printer took a galley of type and scrambled it to make a type specimen book.</p>
<div class="about-photo abs" role="img" aria-label="Photo of a resort pool with a sun lounger, gazebo and palm trees"></div>
<article class="about-card abs">
  <h2>What We Do</h2>
  <p>Lorem Ipsum is simply dummy text of the printing and typesetting industry. Lorem Ipsum has been the industry's standard dummy text ever since the 1500s, when an unknown printer took a galley of type and scrambled</p>
  <a class="btn">Read More</a>
</article>

<svg class="properties-bg abs" viewBox="0 0 1200 935" aria-hidden="true">
  <defs><linearGradient id="pg" x1="0" y1="0" x2="0" y2="1"><stop offset="0" stop-color="#1e1e1e"/><stop offset="1" stop-color="#000"/></linearGradient></defs>
  <polygon points="300,40 620,6 900,40 620,18" fill="#000"/>
  <polygon points="0,98 600,30 1200,98 1200,840 600,922 0,840" fill="url(#pg)"/>
  <polygon points="260,868 600,922 900,868 600,934" fill="#000"/>
</svg>
<h2 class="section-title properties-title abs">Our properties</h2>
<div class="property sky abs" style="left:89px;top:1944px" role="img" aria-label="Photo of a row of new-build brick houses under a blue sky"></div>
<div class="property dark abs listing" style="left:435px;top:1944px">
  <h3>Brookfield's Finest Locations</h3>
  <div class="addr">2150 BROOKFIELD RD ASHBY TOWN,</div>
  <div class="meta">1,200 FQ ST &nbsp;|&nbsp; 12 BEDS &nbsp;|&nbsp; 9 BATHS &nbsp;|&nbsp; 3 GARA</div>
  <div class="price">$7,900,000</div>
  <div class="actions"><i></i><i></i><i></i></div>
</div>
<div class="property sky abs" style="left:780px;top:1944px" role="img" aria-label="Photo of a Tudor-style brick house with a front garden"></div>
<div class="property sky abs" style="left:89px;top:2235px" role="img" aria-label="Photo of a pair of brick semi-detached houses"></div>
<div class="property street abs" style="left:435px;top:2235px" role="img" aria-label="Photo of a terraced street with bay windows"></div>
<div class="property brick abs" style="left:780px;top:2235px" role="img" aria-label="Photo of a red-brick detached house"></div>
<div class="dots abs"><i class="on"></i><i></i><i></i></div>

<h2 class="section-title blog-title abs">Blog</h2>
<div class="blog-card blog-side abs" style="left:-10px;top:2871px;width:152px;height:155px"><div role="img" aria-label="Photo of a dining room interior"></div></div>
<div class="blog-card blog-main abs" style="left:198px;top:2871px;width:440px;height:320px"><div role="img" aria-label="Photo of a lit timber house at dusk"></div></div>
<div class="blog-text abs">
  <h3>Lorem Ipsum</h3>
  <p class="lead">Sed ut perspiciatis unde omnis iste natus error sit voluptatem accusantium doloremque laudantium totam rem aperiam</p>
  <p class="body">Sed ut perspiciatis unde omnis iste natus error sit voluptatem accusantium doloremque laudantium, totam rem aperiam, eaque ipsa quae ab illo inventore veritatis et quasi architecto beatae vitae dicta sunt explicabo.</p>
  <a class="btn">View More</a>
</div>
<div class="blog-card blog-side r abs" style="left:1058px;top:2871px;width:160px;height:155px"><div role="img" aria-label="Photo of a laid dining table"></div></div>
<svg class="arrow abs" style="left:50px;top:3056px" viewBox="0 0 24 24" fill="none" stroke="#1f5fd0" stroke-width="1.5"><circle cx="12" cy="12" r="11"/><path d="M14 7l-5 5 5 5"/></svg>
<svg class="arrow abs" style="left:1120px;top:3056px" viewBox="0 0 24 24" fill="none" stroke="#1f5fd0" stroke-width="1.5"><circle cx="12" cy="12" r="11"/><path d="M10 7l5 5-5 5"/></svg>

<svg class="footer-bg abs" viewBox="0 0 1200 662" aria-hidden="true">
  <polygon points="0,155 572,0 1200,155 1200,160 572,14 0,165" fill="#000"/>
  <polygon points="0,176 572,30 1200,176 1200,662 0,662" fill="#000"/>
</svg>
<footer class="footer">
  <div class="footer-brand abs"><span class="mark"></span>MARTA'S DWELLINGS</div>
  <ul class="contact-list abs">
    <li><svg width="20" height="22" viewBox="0 0 20 24" fill="none" stroke="#fff" stroke-width="1.5"><path d="M10 23s8-8 8-14a8 8 0 0 0-16 0c0 6 8 14 8 14z"/><circle cx="10" cy="9" r="3"/></svg><span>Unit 7, Harbour Court, 12-14 Willow Row, Fenwick, Eastshire, United Kingdom, EX4 9ZQ</span></li>
    <li><svg width="20" height="20" viewBox="0 0 24 24" fill="none" stroke="#fff" stroke-width="1.5"><path d="M5 3h4l2 5-3 2a12 12 0 0 0 6 6l2-3 5 2v4a2 2 0 0 1-2 2A18 18 0 0 1 3 5a2 2 0 0 1 2-2z"/></svg><span>Phone: 555 010 2040</span></li>
    <li><svg width="20" height="16" viewBox="0 0 24 18" fill="none" stroke="#fff" stroke-width="1.5"><rect x="1" y="1" width="22" height="16"/><path d="M1 1l11 9 11-9"/></svg><span>Email:<br>info@martasdwellings-mail.net</span></li>
  </ul>
  <div class="signup abs">
    <h4>SIGN UP TO RECEIVE EMAIL</h4>
    <p>Excepteur sint occaecat cupidatat non proident, sunt in culpa qui Nemo</p>
    <div class="field">Enter Email</div>
    <div class="sub">SUBSCRIBE</div>
  </div>
  <div class="quick-links abs">
    <h4>QUICK LINKS</h4>
    <ul><li>Home</li><li>About Us</li><li>Our Properties</li><li>Blog</li><li>Contact</li></ul>
  </div>
  <div class="footer-rule abs"></div>
  <p class="copyright abs">© 2019Copyrights | Al Rights Reserved</p>
  <div class="social abs"><i></i><i></i><i></i><i></i></div>
</footer>

</body>
</html>
```